Harbor Crestline (Business Card Design)

Need business cards designed. Something modern, chic, and sleek. Mabye the back of the card should be the navy blue that is in the logo and then just the logo on the back.

Target Market(s)

Those in the hotel, office, and renovation industry

Contact Information for Business Card

1. Logo 2. Dorian Fenwick 3. CEO/Founder 4. Phone: (833) HarbCre / (833) 427-2731 5. Email: dorian@theharborcrestline.com 6. Website: www.theharborcrestline.com

Font styles to use
Other font styles liked:
• Look at the logo font and base the font for everything else off of that.

Colors
0054AA
0677BA
7BADD7
CADEEF
E8F1F8

Requirements
Must have
• Colors that are associated in the logo
Nice to have
• Sleek modern clean and chic design.

```html
<!DOCTYPE html>
<html lang="en">
<head>
<meta charset="utf-8">
<title>Harbor Crestline – Business Cards</title>
<link href="https://fonts.googleapis.com/css2?family=Montserrat:wght@600;700&family=Poppins:wght@400;500&display=swap" rel="stylesheet">
<style>
  :root {
    --stage: #2a2a2c;
    --navy: #0d1a4a;
    --navy-deep: #0a1540;
    --gold: #c9a24a;
    --paper: #ffffff;
    --ink: #1b1f2e;
  }
  * { box-sizing: border-box; margin: 0; padding: 0; }
  html, body { width: 1200px; height: 689px; overflow: hidden; }
  body {
    background: var(--stage);
    position: relative;
    font-family: "Poppins", sans-serif;
  }
  .card {
    position: absolute;
    top: 195px;
    width: 525px;
    height: 300px;
    border-radius: 18px;
    overflow: hidden;
    box-shadow: 0 18px 40px rgba(0,0,0,0.45);
  }
  /* Back of card */
  .card-back { left: 42px; background: var(--navy); }
  .card-back .texture {
    position: absolute; inset: 0;
    background: linear-gradient(135deg, #0f1f58 0%, var(--navy-deep) 100%);
  }
  .card-back .brand {
    position: absolute;
    left: 50%; top: 50%;
    transform: translate(-50%, -50%);
    display: flex; align-items: center; gap: 12px;
  }
  .brand-square { width: 18px; height: 18px; }
  .card-back .brand-square { background: var(--paper); }
  .brand-name {
    font-family: "Montserrat", sans-serif;
    font-weight: 700;
    letter-spacing: 0.12em;
    text-transform: uppercase;
    line-height: 1.1;
  }
  .card-back .brand-name { color: var(--paper); font-size: 26px; }

  /* Front of card */
  .card-front { left: 633px; background: var(--paper); }
  .card-front .person {
    position: absolute; right: 34px; top: 44px; text-align: right;
  }
  .person-name {
    font-family: "Montserrat", sans-serif;
    font-weight: 700; font-size: 20px;
    color: var(--navy); letter-spacing: 0.02em;
  }
  .person-role {
    font-family: "Montserrat", sans-serif;
    font-weight: 600; font-size: 12px;
    color: var(--gold); letter-spacing: 0.06em; margin-top: 3px;
  }
  .card-front .brand {
    position: absolute; left: 34px; top: 62px;
    display: flex; align-items: center; gap: 12px;
  }
  .card-front .brand-square { background: var(--navy); width: 22px; height: 22px; }
  .card-front .brand-name { color: var(--navy); font-size: 24px; }

  .contact {
    position: absolute; left: 34px; top: 150px;
    list-style: none;
  }
  .contact li {
    display: flex; align-items: center; gap: 9px;
    font-size: 13px; color: var(--ink); line-height: 1.75;
  }
  .contact svg { width: 13px; height: 13px; fill: var(--navy); flex: none; }

  .band { position: absolute; left: 0; bottom: 0; width: 525px; height: 90px; }
  .band-mark {
    position: absolute; right: 30px; bottom: 30px;
    width: 34px; height: 34px; background: var(--paper);
  }
</style>
</head>
<body>

  <section class="card card-back" aria-label="Card back">
    <div class="texture" role="img" aria-label="Subtle embossed tonal pattern on navy"></div>
    <div class="brand">
      <span class="brand-square"></span>
      <span class="brand-name">Harbor Crestline</span>
    </div>
  </section>

  <section class="card card-front" aria-label="Card front">
    <div class="person">
      <div class="person-name">DORIAN FENWICK</div>
      <div class="person-role">CEO/FOUNDER</div>
    </div>

    <div class="brand">
      <span class="brand-square"></span>
      <span class="brand-name">Harbor<br>Crestline</span>
    </div>

    <ul class="contact">
      <li>
        <svg viewBox="0 0 24 24" aria-hidden="true"><path d="M6.6 10.8a15.1 15.1 0 0 0 6.6 6.6l2.2-2.2c.3-.3.7-.4 1-.2 1.1.4 2.3.6 3.6.6.6 0 1 .4 1 1V20c0 .6-.4 1-1 1C10.6 21 3 13.4 3 4c0-.6.4-1 1-1h3.5c.6 0 1 .4 1 1 0 1.3.2 2.5.6 3.6.1.3 0 .7-.2 1z"/></svg>
        (833) HarbCre / (833) 427-2731
      </li>
      <li>
        <svg viewBox="0 0 24 24" aria-hidden="true"><path d="M2 5h20v14H2zM4 7v.5l8 5 8-5V7l-8 5z"/></svg>
        dorian@theharborcrestline.com
      </li>
      <li>
        <svg viewBox="0 0 24 24" aria-hidden="true"><path d="M12 2a10 10 0 1 0 0 20 10 10 0 0 0 0-20zm6.9 6h-3a15 15 0 0 0-1.3-3.9A8 8 0 0 1 18.9 8zM12 4c.8 1.2 1.5 2.5 1.9 4h-3.8c.4-1.5 1.1-2.8 1.9-4zM4.3 14a8 8 0 0 1 0-4h3.4a16 16 0 0 0 0 4zm.8 2h3a15 15 0 0 0 1.3 3.9A8 8 0 0 1 5.1 16zM8 8H5.1a8 8 0 0 1 4.3-3.9C8.9 5.3 8.4 6.6 8 8zm4 12c-.8-1.2-1.5-2.5-1.9-4h3.8c-.4 1.5-1.1 2.8-1.9 4zm2.3-6H9.7a14 14 0 0 1 0-4h4.6a14 14 0 0 1 0 4zm.3 5.9c.6-1.2 1-2.5 1.3-3.9h3a8 8 0 0 1-4.3 3.9zm1.7-5.9a16 16 0 0 0 0-4h3.4a8 8 0 0 1 0 4z"/></svg>
        www.theharborcrestline.com
      </li>
    </ul>

    <svg class="band" viewBox="0 0 525 90" preserveAspectRatio="none" aria-hidden="true">
      <polygon points="0,68 525,4 525,90 0,90" fill="var(--gold)"/>
      <polygon points="0,74 525,10 525,90 0,90" fill="var(--navy)"/>
    </svg>
    <span class="band-mark"></span>
  </section>

</body>
</html>
```